Market place for used airplanes/helicopters/parts

http://www.vingtorget.se needs a facelift.

# What is it
Classifieds for used airplanes/helicopters/parts/spare parts/aviation literature, for people in Scandinavia. The number of classifieds is ~120-200. They are mainly in Swedish, English, Norwegian.

It's not a glamorous or luxurious business, but more for people with a genuine interest in flying, technical things.

Similar to sites like this, but they have much more classifieds than my site
http://www.skyvendor.com/list/list.aspx?ETID=1&setype=1&catid=6
http://www.lindqvistflyg.com/planes.asp?meny=1&typ=single
https://www.hangarhub.com/cat.php?mode=listing&main=

# What I want
Design only - no code. I want a modern, maybe a bit bootstrap like, clean, simple, not flashy, web design. I want the design to be in English.

# Audience of the website
Aviation interested men, 45-65 years old, in the nordic countries (around Sweden).

# Logotype that could be used (but not necessarily)
http://www.vingtorget.se/flygplan_till_salu_large.jpg
http://www.vingtorget.se/flygplan_till_salu.eps

Reason: I decided to extend the deadline with 1 day. The reason is that I (unfortunately) managed to put the contest in the wrong category for 1 day + I want to give you all feedback (been too busy the whole day, sorry).

Hi all! 

Thanks everyone for the contributions you made. 

I will setup a poll for the designs that I like most. Will get back when I have more information. 

Thanks and have a nice weekend!
Erik

Target Market(s)

45-65 old Scandinavian men

Industry/Entity Type

Business

Requirements
Must have
• - A list with classifieds on the first page, so the visitor easily can see new classifieds.
- A classifieds should be able to have more than one photo
- A simple navigation for showing classifieds from categories like airplanes, helicopters/gyrocopters, parts, literature, misc (maybe other categories) .... but still, it's just 100-200 ads so it's not needed that much filtration.

- A placeholder/way of showing aviation news/clips. In the old design I had, it was a column to the right. It's enough to show maybe 2-5 placeholders.
- A placeholder for PlaceMint ads somewhere on the site.
Should not have
• - Carousels
- Too much clutter

```html
<!DOCTYPE html>
<html lang="en">
<head>
<meta charset="utf-8">
<title>Vingtorget – Aviation Classifieds</title>
<link href="https://fonts.googleapis.com/css2?family=Ubuntu:wght@400;500;700&display=swap" rel="stylesheet">
<style>
:root{
  --navy:#2b3994;
  --cyan:#1fa3cb;
  --hero:#f2f8fc;
  --text:#444;
  --muted:#777;
  --line:#e4e4e4;
  --nav-border:#d9d9d9;
}
*{box-sizing:border-box;margin:0;padding:0}
html,body{width:997px;height:1200px;overflow:hidden;background:#fff;font-family:"Ubuntu",sans-serif;color:var(--text)}
.page{position:relative;width:997px;height:1200px}
.brand{position:absolute;left:166px;top:36px;font-size:22px;font-weight:700;color:var(--navy);letter-spacing:-0.5px;display:flex;align-items:center;gap:8px}
.brand-dot{width:12px;height:12px;background:var(--cyan);border-radius:50%}
.social{position:absolute;left:749px;top:5px;display:flex;gap:3px}
.social span{width:17px;height:17px;border-radius:50%;background:#9aa4ad}
.search{position:absolute;left:664px;top:42px;width:166px;height:20px;border:1px solid #ddd;border-radius:2px;font-size:8px;color:#aaa;padding:5px 12px;box-shadow:inset 1px 1px 2px #eee}
.search svg{position:absolute;right:6px;top:4px}
.hero{position:absolute;left:0;top:77px;width:997px;height:324px;background:var(--hero)}
.nav{position:absolute;left:165px;top:77px;width:666px;height:27px;display:flex;border:1px solid var(--nav-border);border-top:none;background:linear-gradient(#fff,#f3f3f3);font-size:9.5px;color:#444}
.nav a{color:inherit;text-decoration:none;padding:0 11px;line-height:26px;border-right:1px solid var(--nav-border)}
.nav a:last-child{border-right:none}
.hero-art{position:absolute;left:632px;top:116px;width:198px;height:78px;border-radius:40px;background:linear-gradient(90deg,#e3e9ef,#f6f8fa)}
.hero-title{position:absolute;left:165px;top:170px;width:666px;text-align:center;font-size:47px;line-height:40px;font-weight:700;color:var(--navy);letter-spacing:-2.5px}
.hero-lead{position:absolute;left:165px;top:280px;width:666px;text-align:center;font-size:11px;line-height:14.5px;color:var(--cyan)}
.btn-primary{position:absolute;left:429px;top:333px;width:142px;height:32px;background:var(--cyan);color:#fff;font-size:15px;text-align:center;line-height:32px;border-radius:2px}
.top-rule{position:absolute;left:165px;top:401px;width:666px;height:1px;background:var(--line)}
.listings{position:absolute;left:165px;top:412px;width:558px}
.row{position:relative;height:173px;border-bottom:1px solid var(--line)}
.row:last-child{border-bottom:1px solid var(--line)}
.row::before{content:"";position:absolute;left:289px;top:20px;width:1px;height:130px;background:var(--line)}
.ad{position:absolute;top:0;height:173px}
.ad.left{left:0;width:275px}
.ad.right{left:313px;width:245px}
.ad h2{position:absolute;top:8px;left:0;font-size:16px;font-weight:500;color:var(--navy);letter-spacing:-0.6px;white-space:nowrap}
.thumb{position:absolute;left:1px;top:41px;width:94px;height:71px;border:2px solid #ddd}
.details{position:absolute;left:100px;top:42px;font-size:9px;line-height:12px;color:var(--text);letter-spacing:-0.2px}
.details b{font-weight:500;color:#222}
.more{position:absolute;top:127px;right:0;width:74px;height:20px;border:1px solid #ccc;border-radius:2px;background:linear-gradient(#fff,#eee);font-size:9px;text-align:center;line-height:18px;color:#555}
.sidebar{position:absolute;left:750px;top:441px;width:80px}
.banner{display:block;width:80px;margin-bottom:14px}
.footer-bar{position:absolute;left:165px;top:1152px;width:666px;height:4px;background:var(--cyan)}
.footer-links{position:absolute;left:165px;top:1164px;width:666px;text-align:center;font-size:10px;color:#444;word-spacing:2px}
.footer-links a{color:inherit;text-decoration:none;margin:0 3px}
.copyright{position:absolute;left:165px;top:1180px;width:666px;text-align:center;font-size:7.5px;color:var(--muted)}
</style>
</head>
<body>
<div class="page">
  <header>
    <div class="brand"><span class="brand-dot"></span>VINGTORGET</div>
    <div class="social" aria-label="Social links"><span></span><span></span><span></span><span></span></div>
    <div class="search">Search Key Words
      <svg width="10" height="10" viewBox="0 0 10 10"><circle cx="6" cy="4" r="3" fill="none" stroke="#1fa3cb" stroke-width="1.3"/><line x1="4" y1="6" x2="1" y2="9" stroke="#1fa3cb" stroke-width="1.5"/></svg>
    </div>
  </header>

  <section class="hero">
  </section>
  <nav class="nav">
    <a>Home</a><a>Airplanes</a><a>Helicopters/gyrocopters</a><a>Help</a><a>Events</a><a>Parts</a><a>Literature</a><a>Classifieds</a><a>Misc</a>
  </nav>
  <div class="hero-art" role="img" aria-label="Illustration of a white business jet in flight"></div>
  <h1 class="hero-title">IPSUM GENERATORS ON<br>THE INTERNET TEND.</h1>
  <p class="hero-lead">Cras justo odio, dapibus ac facilisis in, egestas eget quam. Fusce dapibus, tellus ac cursus commodo, tortor mauris condimentum nibh, ut fermentum massa justo sit amet risus.</p>
  <div class="btn-primary">Perchase Now</div>
  <div class="top-rule"></div>

  <main class="listings">
    <div class="row">
      <article class="ad left">
        <h2>Vacuum pump</h2>
        <div class="thumb" role="img" aria-label="Photo of a vacuum pump" style="background:linear-gradient(135deg,#c9c4bb,#6b6459)"></div>
        <p class="details"><b>Aerodyne Parts, TT 222 hrs, price 1200<br>SEK</b><br>Name: Sven-Ivar, Email<br>Phone: 0736-518204<br>Date: 2013-10-05 19:31:18</p>
        <span class="more">View details »</span>
      </article>
      <article class="ad right">
        <h2>Veltaro KLS ULC</h2>
        <div class="thumb" role="img" aria-label="Photo of an ultralight aircraft and its cockpit" style="background:linear-gradient(160deg,#9fb0c2,#4d5560)"></div>
        <p class="details"><b>Veltaro KLS ULC</b><br>A unique UL machine in carbon fiber,<br>it makes it exceptionally easy. Empty<br>weight 268kg<br>Manuf. 2006 ca.260 hours, always in<br>hangar.</p>
        <span class="more">View details »</span>
      </article>
    </div>
    <div class="row">
      <article class="ad left">
        <h2>Aerobatic Ravik S-9B LN-QTA</h2>
        <div class="thumb" role="img" aria-label="Aerial photo of an aerobatic plane over an airfield" style="background:linear-gradient(160deg,#8a8e8c,#5c6260)"></div>
        <p class="details">Experimental clipped wing +9/-6G<br>airshow performer for sale in<br>Norway.<br>Phone: +4791230448<br>Date: 2013-10-04 12:23:08</p>
        <span class="more">View details »</span>
      </article>
      <article class="ad right">
        <h2>Pilgrim Corvette 140 Auto STC</h2>
        <div class="thumb" role="img" aria-label="Photo of a small white single-engine plane" style="background:linear-gradient(180deg,#cfd6d8,#8d9a8a)"></div>
        <p class="details">Experimental clipped wing +9/-6G<br>airshow performer for sale in<br>Norway.<br>Phone: +4791230448<br>Date: 2013-10-04 12:23:08</p>
        <span class="more">View details »</span>
      </article>
    </div>
    <div class="row">
      <article class="ad left">
        <h2>LN QXR VR172J 1973 Salg wil!</h2>
        <div class="thumb" role="img" aria-label="Photo of a floatplane on a river by a bridge" style="background:linear-gradient(180deg,#a9b8c4,#4f6a57)"></div>
        <p class="details">We shell reach prave the selge our<br>Vantor 172 rocket 210hp.<br>fluke are on nylakkerte floats.<br>Phone: +4791230448<br>Date: 2013-10-04 12:23:08</p>
        <span class="more">View details »</span>
      </article>
      <article class="ad right">
        <h2>Morlan M6-82/89</h2>
        <div class="thumb" role="img" aria-label="Photo of a floatplane on a lake at dusk" style="background:linear-gradient(180deg,#b4bccb,#55617a)"></div>
        <p class="details">Morlan ML6-235, vm. 1982 brought to<br>Finland in 1989.<br><br>Name: Jussi, Email Phone:<br>+358-44-6120958 Date: 2013-09-30<br>15:21:59</p>
        <span class="more">View details »</span>
      </article>
    </div>
    <div class="row">
      <article class="ad left">
        <h2>Aerobatic Ravik S-9B LN-QTA</h2>
        <div class="thumb" role="img" aria-label="Photo of a large hangar door" style="background:linear-gradient(180deg,#c9ccc4,#8a8468)"></div>
        <p class="details">A place is vacant for a smaller<br>lågvingad plan in our large hangar<br>with 18x4 meter opening.<br>Name: Pelle, Email<br>Phone: 070-418 22 60 0515-20934<br>Date: 2013-09-30 10:07:15</p>
        <span class="more">View details »</span>
      </article>
      <article class="ad right">
        <h2>Aluminum Floats from Anton Brekke.</h2>
        <div class="thumb" role="img" aria-label="Photo of aluminum floats in a workshop" style="background:linear-gradient(180deg,#d8d6d0,#8f8c86)"></div>
        <p class="details">New 1450 lbs floats built by Anton<br>Brekke. Made with pack slots in two<br>floats.<br>Name: Maria Holm, Email<br>Phone: 070-5517302<br>Date: 2013-09-29 18:18:52</p>
        <span class="more">View details »</span>
      </article>
    </div>
  </main>

  <aside class="sidebar">
    <div class="banner" role="img" aria-label="Advert for lipo batteries" style="height:160px;background:linear-gradient(180deg,#1b1b2a,#3a2d12)"></div>
    <div class="banner" role="img" aria-label="Advert for lipo batteries with a red battery pack" style="height:160px;background:linear-gradient(180deg,#fff 0%,#fff 55%,#d63a2f 70%,#a0281f 100%)"></div>
    <div class="banner" role="img" aria-label="Advert for hobby power tools" style="height:152px;background:#141414"></div>
    <div class="banner" role="img" aria-label="Advert for a radio control transmitter" style="height:160px;background:linear-gradient(180deg,#e3741f,#b9561a)"></div>
  </aside>

  <footer>
    <div class="footer-bar"></div>
    <div class="footer-links"><a>Home</a><a>Copyright &amp; Legal Notice</a><a>Privacy Policy</a><a>Site Map</a><a>Contact Us</a></div>
    <p class="copyright">Copyright © by Northwind Publishing Company 2013. All rights reserved.</p>
  </footer>
</div>
</body>
</html>
```